Stonebridge Building and Projects business cards

A business card with watermark background (construction work)

Company logo attached

Home improvement projects
House renovations
Bathroom and kitchen renovations
House extensions
New builds and granny flats

Director Omar Haddani
(Phone number)
omar@sbpbuilding.com.au
(Instagram logo) sbp_building

```html
<!DOCTYPE html>
<html lang="en">
<head>
<meta charset="utf-8">
<title>Stonebridge Building and Projects – Business Cards</title>
<link rel="stylesheet" href="https://fonts.googleapis.com/css2?family=Oswald:wght@500&family=Montserrat:wght@500;600&family=Roboto:wght@400&display=swap">
<style>
  :root {
    --backdrop: #3b3b3c;
    --brand-blue: #3277b6;
    --card-white: #ffffff;
    --text-grey: #4d4d4d;
  }
  * { margin: 0; padding: 0; box-sizing: border-box; }
  html, body {
    width: 1200px; height: 1200px; overflow: hidden;
    background: var(--backdrop);
  }
  .card {
    position: absolute;
    left: 263px;
    width: 685px;
    height: 391px;
  }
  .card--front { top: 165px; background: var(--brand-blue); color: var(--card-white); }
  .card--back  { top: 653px; background: var(--card-white); }

  .person {
    position: absolute;
    right: 430px;
    top: 170px;
    text-align: right;
  }
  .person__name {
    font-family: "Oswald", sans-serif;
    font-weight: 500;
    font-size: 27px;
    line-height: 1;
    letter-spacing: -0.3px;
    text-transform: uppercase;
  }
  .person__role {
    font-family: "Montserrat", sans-serif;
    font-weight: 500;
    font-size: 16px;
    margin-top: 7px;
  }
  .divider {
    position: absolute;
    left: 280px;
    top: 154px;
    width: 1px;
    height: 83px;
    background: var(--card-white);
  }
  .contacts {
    position: absolute;
    left: 302px;
    top: 156px;
    list-style: none;
    font-family: "Montserrat", sans-serif;
    font-weight: 500;
    font-size: 16px;
  }
  .contacts li {
    display: flex;
    align-items: center;
    height: 19.6px;
  }
  .contacts svg { width: 12px; height: 12px; margin-right: 9px; flex: none; }

  .brand {
    position: absolute;
    left: 0; right: 0;
    top: 95px;
    display: flex;
    flex-direction: column;
    align-items: center;
    text-align: center;
    font-family: "Montserrat", sans-serif;
    font-weight: 600;
    color: var(--brand-blue);
    font-size: 30px;
    line-height: 1.2;
  }
  .brand__mark {
    width: 26px; height: 26px;
    background: var(--brand-blue);
    margin-bottom: 16px;
  }
  .services {
    position: absolute;
    left: 0; right: 0;
    top: 318px;
    text-align: center;
    font-family: "Roboto", sans-serif;
    font-size: 16px;
    line-height: 19px;
    color: var(--text-grey);
  }
  .services .sep {
    display: inline-block;
    width: 6px; height: 6px;
    margin: 0 8px 2px;
    background:
      radial-gradient(circle, var(--brand-blue) 1px, transparent 1.3px) 0 0 / 3px 3px;
  }
</style>
</head>
<body>

<section class="card card--front">
  <div class="person">
    <div class="person__name">Omar Haddani</div>
    <div class="person__role">Director</div>
  </div>
  <div class="divider"></div>
  <ul class="contacts">
    <li>
      <svg viewBox="0 0 24 24" aria-hidden="true"><path fill="#fff" d="M6.6 10.8a15.1 15.1 0 0 0 6.6 6.6l2.2-2.2c.3-.3.7-.4 1-.2 1.1.4 2.3.6 3.6.6.6 0 1 .4 1 1V20c0 .6-.4 1-1 1A17 17 0 0 1 3 4c0-.6.4-1 1-1h3.5c.6 0 1 .4 1 1 0 1.3.2 2.5.6 3.6.1.3 0 .7-.2 1z"/></svg>
      402-318-7754
    </li>
    <li>
      <svg viewBox="0 0 24 24" aria-hidden="true"><path fill="#fff" d="M2 5h20v14H2z"/><path d="M2 5l10 8 10-8" fill="none" stroke="#3277b6" stroke-width="2"/></svg>
      omar@sbpbuilding.com.au
    </li>
    <li>
      <svg viewBox="0 0 24 24" aria-hidden="true"><circle cx="12" cy="12" r="10" fill="#fff"/><path d="M2 12h20M12 2c3 3 3 17 0 20M12 2c-3 3-3 17 0 20" fill="none" stroke="#3277b6" stroke-width="1.6"/></svg>
      sbpbuilding.com.au
    </li>
    <li>
      <svg viewBox="0 0 24 24" aria-hidden="true"><circle cx="12" cy="12" r="9" fill="none" stroke="#fff" stroke-width="3"/></svg>
      sbp_building
    </li>
  </ul>
</section>

<section class="card card--back">
  <div class="brand">
    <span class="brand__mark"></span>
    <span>Stonebridge Building</span>
    <span>and Projects</span>
  </div>
  <p class="services">
    Home improvement projects<span class="sep"></span>House renovations<span class="sep"></span>House extensions<br>
    Bathroom &amp; kitchen renovations<span class="sep"></span>New builds &amp; granny flats
  </p>
</section>

</body>
</html>
```